credit repair e book mockup

I'm in need of a credit eBook mock up. basic graphics for credit can be used. like credit score meters etc.

PLEASE SEE ATTACHED EXAMPLES

i would like the text to include these phrases; DIY credit e-book, all the things you cant google about credit, step by step guide to repair and leverage your credit to fund your goals!

The name of the company is Bright Harbor Financial Consultants
Can be abbreviated to BHF Consultants

```html
<!DOCTYPE html>
<html lang="en">
<head>
<meta charset="utf-8">
<title>DIY Credit Repair Guide – Social Posts</title>
<link href="https://fonts.googleapis.com/css2?family=Lato:wght@400;700;900&family=Montserrat:wght@500;700;800&family=Dancing+Script:wght@700&display=swap" rel="stylesheet">
<style>
  :root {
    --sheet: #ececec;
    --ink: #141414;
    --black: #1c1c1c;
    --red: #e30613;
    --red-soft: #e03a3a;
    --green: #7cb342;
    --yellow: #f9b234;
    --white: #ffffff;
  }
  * { margin: 0; padding: 0; box-sizing: border-box; }
  html, body { width: 1200px; height: 3456px; overflow: hidden; }
  body { background: var(--sheet); font-family: "Lato", sans-serif; position: relative; }

  .post {
    position: absolute; left: 121px; width: 960px; height: 960px;
    overflow: hidden; background: var(--ink);
    box-shadow: 0 18px 22px -8px rgba(0,0,0,.45);
  }
  .post--green { top: 105px; background: var(--black); }
  .post--red { top: 1233px; background: #000; }
  .post--yellow { top: 2362px; background: var(--yellow); }

  .shape { position: absolute; inset: 0; width: 960px; height: 960px; }

  .brand {
    position: absolute; font-family: "Lato", sans-serif; font-weight: 700;
    text-transform: uppercase; line-height: 1.15; letter-spacing: .5px;
  }
  .brand span { display: block; }

  .title { position: absolute; text-transform: uppercase; }
  .title__diy { font-family: "Lato", sans-serif; font-weight: 400; font-size: 62px; color: var(--white); line-height: 1; }
  .title__main { font-family: "Lato", sans-serif; font-weight: 900; font-size: 60px; line-height: 1.1; }
  .title__guide { font-family: "Montserrat", sans-serif; font-weight: 700; font-size: 52px; letter-spacing: 27px; color: var(--white); line-height: 1.1; }

  .taglines { position: absolute; color: var(--white); font-weight: 700; text-transform: uppercase; font-size: 27px; line-height: 1.25; }
  .taglines p + p { margin-top: 14px; }

  .website { position: absolute; font-family: "Montserrat", sans-serif; font-weight: 500; font-size: 19px; letter-spacing: 4px; text-transform: uppercase; }

  .mockup { position: absolute; border-radius: 6px; }

  /* post 1 */
  .post--green .brand { right: 24px; top: 96px; text-align: right; color: var(--ink); font-size: 22px; }
  .post--green .title { left: 50px; top: 84px; }
  .post--green .title__main { color: var(--green); margin-top: 8px; }
  .post--green .mockup { left: 199px; top: 284px; width: 501px; height: 396px;
    background: linear-gradient(135deg, #3a3a3a 0%, #262626 55%, #4a4a4a 100%); }
  .post--green .taglines { left: 50px; top: 708px; }
  .post--green .website { left: 50px; top: 904px; color: var(--white); }

  /* post 2 */
  .post--red .brand { left: 0; right: 0; top: 78px; text-align: center; color: var(--red-soft); font-size: 21px; }
  .post--red .title { left: 154px; top: 122px; }
  .post--red .title__main { color: var(--red-soft); font-size: 64px; margin-top: 6px; }
  .post--red .title__guide { font-size: 56px; letter-spacing: 30px; }
  .post--red .rule { position: absolute; left: 134px; top: 348px; width: 689px; height: 3px; background: var(--red); }
  .post--red .taglines { left: 152px; top: 370px; }
  .post--red .mockup { left: 199px; top: 507px; width: 501px; height: 395px;
    background: linear-gradient(135deg, #2a2a2a 0%, #111 50%, #3a3a3a 100%); }
  .post--red .website { left: 0; right: 0; top: 922px; text-align: center; color: var(--white); }

  /* post 3 */
  .post--yellow .brand { left: 0; right: 0; top: 60px; text-align: center; color: var(--red); font-size: 15px; }
  .post--yellow .band { position: absolute; left: 0; top: 104px; width: 960px; height: 39px; background: var(--white);
    text-align: center; font-family: "Montserrat", sans-serif; font-weight: 700; color: var(--red);
    font-size: 25px; letter-spacing: 6px; line-height: 39px; text-transform: uppercase; }
  .post--yellow .stack { position: absolute; left: 0; right: 0; top: 156px; text-align: center; text-transform: uppercase; }
  .post--yellow .stack__credit { font-family: "Montserrat", sans-serif; font-weight: 800; font-size: 90px; color: var(--red); line-height: 1; }
  .post--yellow .stack__repair { font-family: "Montserrat", sans-serif; font-weight: 800; font-size: 46px; letter-spacing: 12px; color: var(--white); line-height: 1.15; }
  .post--yellow .stack__ebook { font-family: "Dancing Script", cursive; font-weight: 700; font-size: 54px; color: var(--ink); text-transform: none; line-height: 1; }
  .post--yellow .mockup { left: 228px; top: 403px; width: 450px; height: 365px;
    background: linear-gradient(135deg, #2b2b2b 0%, #1a1a1a 55%, #c8352a 100%); }
  .post--yellow .taglines { left: 186px; top: 786px; }
  .post--yellow .website { right: 80px; top: 921px; color: var(--red); }
</style>
</head>
<body>

<section class="post post--green">
  <svg class="shape" viewBox="0 0 960 960" aria-hidden="true">
    <polygon points="510,0 960,0 960,452" fill="var(--red)"/>
    <polygon points="0,506 0,960 456,960" fill="var(--red)"/>
  </svg>
  <div class="brand"><span>Bright Harbor Financial</span><span>Consultants</span></div>
  <div class="title">
    <div class="title__diy">DIY</div>
    <div class="title__main">Credit Repair</div>
    <div class="title__guide">Guide</div>
  </div>
  <div class="mockup" role="img" aria-label="E-book shown on a tablet, a phone and as a hardcover book, with a credit card and wrench graphic"></div>
  <div class="taglines">
    <p>All the things you can’t look up about credit</p>
    <p>Step by step guide to repair and leverage your<br>credit to fund your goals!</p>
  </div>
  <div class="website">www. bhfguide.example</div>
</section>

<section class="post post--red">
  <svg class="shape" viewBox="0 0 960 960" aria-hidden="true">
    <path d="M0 960 A503 503 0 0 1 960 960 Z" fill="var(--red)"/>
  </svg>
  <div class="brand"><span>Bright Harbor Financial</span><span>Consultants</span></div>
  <div class="title">
    <div class="title__diy">DIY</div>
    <div class="title__main">Credit Repair</div>
    <div class="title__guide">Guide</div>
  </div>
  <div class="rule"></div>
  <div class="taglines">
    <p>All the things you can’t look up about credit</p>
    <p>Step by step guide to repair and leverage your<br>credit to fund your goals!</p>
  </div>
  <div class="mockup" role="img" aria-label="E-book shown on a tablet, a phone and as a hardcover book, with a dollar sign and tools graphic"></div>
  <div class="website">www. bhfguide.example</div>
</section>

<section class="post post--yellow">
  <svg class="shape" viewBox="0 0 960 960" aria-hidden="true">
    <polygon points="403,0 960,0 960,557" fill="var(--black)"/>
    <polygon points="0,362 597,960 0,960" fill="var(--black)"/>
  </svg>
  <div class="brand"><span>Bright Harbor Financial</span><span>Consultants</span></div>
  <div class="band">Do it yourself</div>
  <div class="stack">
    <div class="stack__credit">Credit</div>
    <div class="stack__repair">Repair</div>
    <div class="stack__ebook">ebook</div>
  </div>
  <div class="mockup" role="img" aria-label="E-book shown on a tablet, a phone and as a hardcover book, with a rising bar chart and arrow graphic"></div>
  <div class="taglines">
    <p>All the things you can’t look up about credit</p>
    <p>Step by step guide to repair and leverage your<br>credit to fund your goals!</p>
  </div>
  <div class="website">www. bhfguide.example</div>
</section>

</body>
</html>
```